Business Card Design for Property Development Company Director

I am looking for a professional and unforgettable business card design for our Director of our Property Development Company.
Please see attached .pptx file to find out what information to include. You don't have to follow the exact format shown in the file - I am interested to see your creative flair using the information provided.

```html
<!DOCTYPE html>
<html lang="en">
<head>
<meta charset="utf-8">
<title>Harwell Property Group – Business Card</title>
<link rel="stylesheet" href="https://fonts.googleapis.com/css2?family=Arimo:wght@400;700&display=swap">
<style>
  :root {
    --bg: #1e1f22;
    --card: #ffffff;
    --brand-blue: #1a5ca8;
    --ink-grey: #4a4a4c;
    --rule-grey: #c9c9c9;
  }
  * { box-sizing: border-box; margin: 0; padding: 0; }
  html, body { width: 1200px; height: 800px; overflow: hidden; }
  body {
    background: var(--bg);
    font-family: "Arimo", Arial, sans-serif;
    position: relative;
  }
  .card {
    position: absolute;
    width: 560px;
    height: 340px;
    background: var(--card);
    overflow: hidden;
    box-shadow: 0 18px 40px rgba(0,0,0,.45);
  }
  .card--front { left: 40px; top: 60px; }
  .card--back { left: 600px; top: 400px; }

  /* Front */
  .tagline {
    position: absolute; left: 60px; top: 62px;
    font-weight: 700; font-size: 19px; line-height: 1.35;
    color: var(--ink-grey); letter-spacing: .5px; text-transform: uppercase;
  }
  .brand__square { position: absolute; background: var(--ink-grey); }
  .brand__name {
    position: absolute;
    font-weight: 700; color: var(--ink-grey); text-transform: uppercase;
    line-height: 1.05;
  }
  .brand__name span { display: block; letter-spacing: 3.5px; }
  .card--front .brand__square { left: 60px; top: 150px; width: 54px; height: 54px; }
  .card--front .brand__name { left: 128px; top: 152px; font-size: 30px; }
  .card--front .brand__name span { font-size: 15px; }
  .invite {
    position: absolute; left: 60px; bottom: 58px;
    font-size: 13px; color: var(--ink-grey);
  }
  .invite strong { font-weight: 700; }

  /* Back */
  .band { position: absolute; inset: 0; }
  .card--back .brand__square { left: 40px; top: 52px; width: 64px; height: 64px; background: var(--card); }
  .card--back .brand__name { left: 182px; top: 56px; font-size: 32px; }
  .card--back .brand__name span { font-size: 16px; }
  .contact { position: absolute; left: 262px; top: 158px; }
  .contact__name {
    font-weight: 700; font-size: 19px; color: var(--ink-grey); text-transform: uppercase;
  }
  .contact__name b { color: var(--brand-blue); }
  .contact__role { font-size: 15px; color: var(--brand-blue); margin-bottom: 12px; }
  .contact__list { list-style: none; font-size: 13px; color: var(--ink-grey); }
  .contact__list li { display: flex; align-items: center; gap: 8px; margin-bottom: 5px; }
  .contact__list svg { width: 13px; height: 13px; fill: var(--brand-blue); flex: none; }
  .licence { margin-top: 6px; font-size: 13px; color: var(--brand-blue); }
</style>
</head>
<body>

<section class="card card--front">
  <p class="tagline">Property Development<br>&amp; Site Acquisition Specialists</p>
  <div class="brand__square"></div>
  <p class="brand__name">Harwell<span>Property Group</span></p>
  <p class="invite">Ask me about our <strong>INVESTMENT &amp; PARTNERSHIP</strong> opportunities</p>
</section>

<section class="card card--back">
  <svg class="band" viewBox="0 0 560 340" aria-hidden="true">
    <polygon points="0,0 128,0 230,340 0,340" fill="var(--brand-blue)"/>
    <line x1="135" y1="0" x2="237" y2="340" stroke="var(--rule-grey)" stroke-width="2"/>
  </svg>
  <div class="brand__square"></div>
  <p class="brand__name">Harwell<span>Property Group</span></p>
  <div class="contact">
    <p class="contact__name">Daniel <b>Marsh</b></p>
    <p class="contact__role">Director</p>
    <ul class="contact__list">
      <li><svg viewBox="0 0 16 16"><path d="M3 1h3l1.5 4-2 1.5a9 9 0 0 0 4 4l1.5-2 4 1.5v3c0 1-1 2-2 2A13 13 0 0 1 1 3c0-1 1-2 2-2z"/></svg>0400 123 456</li>
      <li><svg viewBox="0 0 16 16"><path d="M1 3h14v10H1z M1 3l7 6 7-6" fill="none" stroke="var(--brand-blue)" stroke-width="1.6"/></svg>daniel@harwellgroup.com.au</li>
      <li><svg viewBox="0 0 16 16"><circle cx="8" cy="8" r="6.5" fill="none" stroke="var(--brand-blue)" stroke-width="1.4"/><path d="M1.5 8h13M8 1.5c-3 3.5-3 9.5 0 13M8 1.5c3 3.5 3 9.5 0 13" fill="none" stroke="var(--brand-blue)" stroke-width="1.2"/></svg>www.harwellgroup.com.au</li>
    </ul>
    <p class="licence">Real Estate Lic. 1234567 &amp; 1234568</p>
  </div>
</section>

</body>
</html>
```